Criação de Kit Layout de Posts para Redes Sociais (Facebook, Instagram e etc) para Outros
A empresa queria:
" empresa segmentada na área corporativa "

```html
<!DOCTYPE html>
<html lang="pt-BR">
<head>
<meta charset="UTF-8">
<title>Vortel Telecom – Planos a partir de 89,90</title>
<link rel="stylesheet" href="https://fonts.googleapis.com/css2?family=Roboto+Condensed:ital,wght@0,700;1,700&display=swap">
<style>
  :root {
    --sky: #2a8fd4;
    --lime: #8cc63f;
    --navy: #0e3a5e;
    --paper: #f4f8fb;
    --white: #ffffff;
  }
  html, body {
    margin: 0;
    padding: 0;
    width: 1200px;
    height: 1200px;
    overflow: hidden;
    background: var(--paper);
  }
  .post {
    position: relative;
    width: 1200px;
    height: 1200px;
    overflow: hidden;
    background: linear-gradient(180deg, #ffffff 0%, #eef4f9 45%, #e6edf3 100%);
    font-family: "Roboto Condensed", "Arial Narrow", sans-serif;
  }
  .scene-photo {
    position: absolute;
    left: 0;
    top: 380px;
    width: 1200px;
    height: 820px;
    background:
      radial-gradient(ellipse 520px 380px at 960px 300px, rgba(40,40,44,0.85), rgba(40,40,44,0) 70%),
      radial-gradient(ellipse 420px 260px at 520px 420px, rgba(190,196,204,0.9), rgba(190,196,204,0) 70%),
      radial-gradient(ellipse 300px 220px at 620px 260px, rgba(196,150,120,0.7), rgba(196,150,120,0) 70%),
      linear-gradient(180deg, rgba(230,236,242,0) 0%, #b8a492 55%, #8a735f 100%);
  }
  .headline {
    position: absolute;
    left: 96px;
    top: 70px;
    margin: 0;
    font-style: italic;
    font-weight: 700;
    font-size: 74px;
    line-height: 84px;
    text-transform: uppercase;
    letter-spacing: 0.5px;
  }
  .headline .line-one { color: var(--sky); display: block; }
  .headline .line-two { color: var(--lime); display: block; }
  .offer {
    position: absolute;
    left: 96px;
    top: 290px;
    color: var(--navy);
    font-weight: 700;
    text-transform: uppercase;
  }
  .offer .plans {
    display: block;
    font-size: 120px;
    line-height: 110px;
  }
  .offer .from {
    display: block;
    font-size: 42px;
    line-height: 46px;
    margin-top: 4px;
  }
  .offer .price {
    display: block;
    color: var(--sky);
    font-size: 210px;
    line-height: 180px;
    margin-top: 4px;
    letter-spacing: -2px;
  }
  .offer .price .cents {
    font-size: 104px;
    letter-spacing: 0;
  }
  .bands {
    position: absolute;
    left: 0;
    bottom: 0;
    width: 1200px;
    height: 280px;
  }
  .brand {
    position: absolute;
    left: 0;
    width: 1200px;
    bottom: 62px;
    text-align: center;
    color: var(--white);
    font-weight: 700;
    font-size: 50px;
    line-height: 56px;
  }
  .brand .mark {
    display: inline-block;
    width: 26px;
    height: 26px;
    border-radius: 50%;
    background: var(--white);
    margin-left: 12px;
    vertical-align: middle;
  }
</style>
</head>
<body>
  <main class="post">
    <div class="scene-photo" role="img" aria-label="Foto de pessoa usando notebook e celular sobre uma mesa de escritório"></div>

    <h1 class="headline">
      <span class="line-one">Você merece a</span>
      <span class="line-two">melhor conexão!</span>
    </h1>

    <p class="offer">
      <span class="plans">Planos</span>
      <span class="from">A partir de</span>
      <span class="price">89<span class="cents">,90</span></span>
    </p>

    <svg class="bands" viewBox="0 0 1200 280" aria-hidden="true">
      <path d="M0 120 C 260 60, 560 90, 820 110 C 980 122, 1100 90, 1200 40 L1200 280 L0 280 Z" fill="#2a8fd4" opacity="0.55"/>
      <path d="M620 230 C 820 180, 1020 120, 1200 60 L1200 280 L560 280 Z" fill="#8cc63f"/>
      <path d="M0 150 C 240 100, 520 130, 760 150 C 900 162, 980 170, 1040 190 C 900 240, 780 270, 700 280 L0 280 Z" fill="#2a8fd4"/>
    </svg>

    <div class="brand">Vortel Telecom<span class="mark"></span></div>
  </main>
</body>
</html>
```